Marrowby Water Taxi and Transport Business Card

I need business cards for my new water taxi and freight transport business I have started here in Kodiak Alaska. Kodiak is a remote island in the middle of the gulf of Alaska. There are seven native villages around the island and Kodiak is the #2 fishing port in the United States. We also have the largest Coast Guard Base in the U.S. My company will be providing water taxi and freight transport logistics to the villages and many hunting and fishing lodges as well as remote properties around the island.

I would like a business card that isn't status quo, something that stands out, either in feel or appearance. I do like clean minimal designs but it needs to have the necessary contact info on it.

Target Market(s)

remote lodge / property owners, residents of the many villages around Kodiak and any one wanting to enjoy the great outdoors of Kodiak Alaska

Industry/Entity Type

Business

Contact Information for Business Card

I like clean simple designs that aren't cluttered but still provide the necessary information

Colors
0255a3
3277b5
33a4d5
9bcb3c
add136
fbed22
ffc214
f78f20
f37122

Requirements
Must have
• logo and contact info
• Captain Mason Elwick
• www.marrowbyferryline.com
• mason@marrowbyferryline.com

```html
<!DOCTYPE html>
<html lang="en">
<head>
<meta charset="utf-8">
<title>Marrowby Water Taxi and Transport – Business Card</title>
<link rel="stylesheet" href="https://fonts.googleapis.com/css2?family=Open+Sans:wght@400;600;700&display=swap">
<style>
  :root {
    --backdrop: #8c8c8c;
    --card-white: #ffffff;
    --sky-blue: #25a5de;
    --brand-blue: #0255a3;
    --sun-orange: #f78f20;
    --text-white: #ffffff;
  }
  * { margin: 0; padding: 0; box-sizing: border-box; }
  html, body { width: 1200px; height: 900px; overflow: hidden; }
  body {
    background: var(--backdrop);
    font-family: "Open Sans", Arial, sans-serif;
    position: relative;
  }
  .card {
    position: absolute;
    left: 250px;
    width: 700px;
    height: 400px;
    background: var(--card-white);
    overflow: hidden;
  }
  .card--front { top: 35px; }
  .card--back { top: 465px; background: var(--sky-blue); }

  .brand {
    position: absolute;
    inset: 0;
    display: flex;
    align-items: center;
    justify-content: center;
    gap: 18px;
  }
  .brand__mark {
    width: 46px;
    height: 46px;
    border-radius: 50%;
    background: var(--sun-orange);
    flex: none;
  }
  .brand__name {
    color: var(--brand-blue);
    font-weight: 700;
    font-size: 30px;
    line-height: 1.2;
  }

  .card__shape { position: absolute; inset: 0; }

  .brand--panel {
    inset: auto;
    left: 30px;
    top: 120px;
    width: 220px;
    justify-content: flex-start;
    gap: 12px;
  }
  .brand--panel .brand__mark { width: 30px; height: 30px; }
  .brand--panel .brand__name { font-size: 19px; }

  .contact {
    position: absolute;
    right: 44px;
    top: 120px;
    color: var(--text-white);
    display: flex;
    flex-direction: column;
    align-items: flex-end;
  }
  .contact__name {
    font-weight: 700;
    font-size: 24px;
    margin-bottom: 48px;
    white-space: nowrap;
  }
  .contact__line {
    display: flex;
    align-items: center;
    gap: 12px;
    font-size: 16px;
    line-height: 30px;
    white-space: nowrap;
  }
  .contact__icon { width: 14px; height: 14px; flex: none; }
</style>
</head>
<body>
  <section class="card card--front" aria-label="Card front">
    <div class="brand">
      <span class="brand__mark"></span>
      <span class="brand__name">Marrowby<br>Water Taxi and Transport</span>
    </div>
  </section>

  <section class="card card--back" aria-label="Card back">
    <svg class="card__shape" viewBox="0 0 700 400" aria-hidden="true">
      <polygon points="0,0 225,0 250,28 385,228 95,400 0,400" fill="#ffffff"/>
      <polyline points="225,0 250,28 385,228 95,400" fill="none" stroke="#f78f20" stroke-width="5"/>
    </svg>

    <div class="brand brand--panel">
      <span class="brand__mark"></span>
      <span class="brand__name">Marrowby<br>Water Taxi and Transport</span>
    </div>

    <div class="contact">
      <p class="contact__name">Captain Mason Elwick</p>
      <p class="contact__line">
        <span>mason@marrowbyferryline.com</span>
        <svg class="contact__icon" viewBox="0 0 24 24" aria-hidden="true"><path fill="#fff" d="M6.6 10.8a15 15 0 0 0 6.6 6.6l2.2-2.2c.3-.3.7-.4 1-.2 1.1.4 2.3.6 3.6.6.6 0 1 .4 1 1V20c0 .6-.4 1-1 1A17 17 0 0 1 3 4c0-.6.4-1 1-1h3.5c.6 0 1 .4 1 1 0 1.3.2 2.5.6 3.6.1.3 0 .7-.2 1z"/></svg>
      </p>
      <p class="contact__line">
        <span>www.marrowbyferryline.com</span>
        <svg class="contact__icon" viewBox="0 0 24 24" aria-hidden="true"><rect x="2" y="5" width="20" height="14" fill="#fff"/><polyline points="2,5 12,13 22,5" fill="none" stroke="#25a5de" stroke-width="1.6"/></svg>
      </p>
    </div>
  </section>
</body>
</html>
```